Landscape design build company door flyer

I would like this flyer to convey a high-level of professionalism for a company that is excellent with communication with their clients as well as a company that does incredible installations

Went on vacation/holiday

```html
<!DOCTYPE html>
<html lang="en">
<head>
<meta charset="utf-8">
<title>Cedarline Builders – Outdoor Living Flyer</title>
<link href="https://fonts.googleapis.com/css2?family=Barlow+Condensed:wght@700;800&family=Barlow:wght@800&family=Poppins:wght@400;500;700;800&display=swap" rel="stylesheet">
<style>
:root{
  --navy:#0b2a40;
  --orange:#f46d0a;
  --gold:#f2a516;
  --paper:#f1f1f1;
  --ink:#1d1d1d;
  --white:#ffffff;
  --backdrop:#e4e4e4;
}
*{margin:0;padding:0;box-sizing:border-box}
html,body{width:1200px;height:1029px;overflow:hidden;background:var(--backdrop)}
.stage{position:relative;width:1200px;height:1029px}
.flyer-frame{position:absolute;left:215px;top:20px;width:770px;height:990px;overflow:hidden}
.flyer{position:absolute;left:0;top:0;width:1273px;height:1637px;background:var(--paper);transform:scale(0.6048);transform-origin:0 0;font-family:"Poppins",sans-serif;color:var(--ink)}
.shapes{position:absolute;left:0;top:0;width:1273px;height:1637px}
.brand{position:absolute;left:0;top:170px;width:500px;text-align:center;display:flex;justify-content:center;align-items:center;gap:14px}
.brand-dot{width:22px;height:22px;border-radius:50%;background:var(--orange)}
.brand-name{font-family:"Poppins",sans-serif;font-weight:700;font-size:32px;color:var(--orange);letter-spacing:1px}
.headline{position:absolute;left:58px;top:328px;font-family:"Barlow Condensed",sans-serif;font-weight:800;font-size:98px;line-height:93.5px;letter-spacing:0.5px;color:var(--white)}
.headline .accent{color:var(--orange)}
.section-title{position:absolute;top:798px;font-family:"Poppins",sans-serif;font-weight:800;font-size:40px;letter-spacing:-0.5px;color:var(--navy)}
.section-title::after{content:"";position:absolute;left:0;top:54px;width:110px;height:5px;border-radius:3px;background:var(--gold)}
.about-title{left:58px}
.services-title{left:701px}
.about-text{position:absolute;left:56px;top:870px;width:540px;font-size:20.5px;line-height:24.4px;text-align:justify;color:var(--ink)}
.service-list{position:absolute;left:700px;top:868px;list-style:none}
.service-list li{display:flex;align-items:center;height:34.5px;font-size:22.5px;font-weight:500;color:var(--navy)}
.service-list svg{width:20px;height:20px;margin-right:26px}
.works-rule{position:absolute;left:40px;top:1176px;width:1190px;height:2px;background:var(--gold)}
.works-tag{position:absolute;left:450px;top:1148px;width:360px;height:49px;background:var(--orange);color:var(--white);font-weight:800;font-size:30px;text-align:center;line-height:49px}
.work-photo{position:absolute;top:1220px;width:344px;height:187px}
.work-deck{left:62px;background:linear-gradient(180deg,#4f8a3a 0%,#3d6a2c 40%,#9a4e2e 62%,#7a3a22 100%)}
.work-pool{left:454px;background:radial-gradient(ellipse at 45% 50%,#3fc6c0 0%,#7fa8a8 30%,#c9d0d2 55%,#b8c0c2 100%)}
.work-firepit{left:847px;background:linear-gradient(180deg,#3a4a3a 0%,#4b5360 35%,#5a5250 65%,#3f3632 100%)}
.hero-photo{position:absolute;left:0;top:0;width:1273px;height:770px}
.phone-box{position:absolute;left:60px;top:1516px;width:84px;height:83px;background:var(--orange);display:flex;align-items:center;justify-content:center}
.phone-number{position:absolute;left:160px;top:1502px;font-family:"Barlow",sans-serif;font-weight:800;font-size:82px;line-height:110px;color:var(--white);letter-spacing:1px}
.contact{position:absolute;left:832px;display:flex;align-items:center;font-size:25px;color:var(--white)}
.contact svg{width:30px;height:30px;margin-right:30px}
.contact-email{top:1505px}
.contact-web{top:1547px}
</style>
</head>
<body>
<div class="stage">
  <div class="flyer-frame">
    <div class="flyer">
      <svg class="shapes" viewBox="0 0 1273 1637" aria-hidden="true">
        <rect x="0" y="260" width="900" height="510" fill="var(--navy)"/>
        <polygon points="0,1486 771,1486 706,1637 0,1637" fill="var(--navy)"/>
        <polygon points="776,1474 1273,1474 1273,1637 706,1637" fill="var(--orange)"/>
      </svg>

      <svg class="hero-photo" viewBox="0 0 1273 770" role="img" aria-label="Aerial photo of a two-storey house with a new paver driveway, walkway and planting beds">
        <defs>
          <linearGradient id="heroTone" x1="0" y1="0" x2="1" y2="1">
            <stop offset="0" stop-color="#5b7a3a"/>
            <stop offset="0.35" stop-color="#6c7278"/>
            <stop offset="0.7" stop-color="#5d5f62"/>
            <stop offset="1" stop-color="#4a3a30"/>
          </linearGradient>
        </defs>
        <polygon points="586,0 1273,0 1273,770 849,770 591,260 494,260" fill="url(#heroTone)"/>
      </svg>

      <div class="brand">
        <span class="brand-dot"></span>
        <span class="brand-name">CEDARLINE BUILDERS</span>
      </div>

      <h1 class="headline">LET’S CREATE<br>YOUR DREAM<br><span class="accent">OUTDOOR<br>LIVING SPACE!</span></h1>

      <h2 class="section-title about-title">ABOUT US</h2>
      <p class="about-text">Discover the endless possibilities for your outdoor space with The Cedarline Builders Team. Our team of skilled artisans is dedicated to turning your outdoor space into a breathtaking oasis that you’ll love coming home to. Whether it’s a cozy patio for intimate gatherings, a sprawling deck to host memorable parties, or a custom paver driveway that adds instant curb appeal, our high-quality craftsmanship ensures stunning results that exceed your expectations.</p>

      <h2 class="section-title services-title">OUR SERVICES</h2>
      <ul class="service-list">
        <li><svg viewBox="0 0 20 20"><circle cx="10" cy="10" r="10" fill="var(--orange)"/><path d="M5.5 10.3l3 3 6-6.3" stroke="#fff" stroke-width="2.4" fill="none" stroke-linecap="round" stroke-linejoin="round"/></svg>Paver Patios</li>
        <li><svg viewBox="0 0 20 20"><circle cx="10" cy="10" r="10" fill="var(--orange)"/><path d="M5.5 10.3l3 3 6-6.3" stroke="#fff" stroke-width="2.4" fill="none" stroke-linecap="round" stroke-linejoin="round"/></svg>Paver Driveways</li>
        <li><svg viewBox="0 0 20 20"><circle cx="10" cy="10" r="10" fill="var(--orange)"/><path d="M5.5 10.3l3 3 6-6.3" stroke="#fff" stroke-width="2.4" fill="none" stroke-linecap="round" stroke-linejoin="round"/></svg>Retaining Walls</li>
        <li><svg viewBox="0 0 20 20"><circle cx="10" cy="10" r="10" fill="var(--orange)"/><path d="M5.5 10.3l3 3 6-6.3" stroke="#fff" stroke-width="2.4" fill="none" stroke-linecap="round" stroke-linejoin="round"/></svg>Decks &amp; Railings</li>
        <li><svg viewBox="0 0 20 20"><circle cx="10" cy="10" r="10" fill="var(--orange)"/><path d="M5.5 10.3l3 3 6-6.3" stroke="#fff" stroke-width="2.4" fill="none" stroke-linecap="round" stroke-linejoin="round"/></svg>Pools</li>
        <li><svg viewBox="0 0 20 20"><circle cx="10" cy="10" r="10" fill="var(--orange)"/><path d="M5.5 10.3l3 3 6-6.3" stroke="#fff" stroke-width="2.4" fill="none" stroke-linecap="round" stroke-linejoin="round"/></svg>Outdoor Lighting</li>
        <li><svg viewBox="0 0 20 20"><circle cx="10" cy="10" r="10" fill="var(--orange)"/><path d="M5.5 10.3l3 3 6-6.3" stroke="#fff" stroke-width="2.4" fill="none" stroke-linecap="round" stroke-linejoin="round"/></svg>Firepits &amp; Fireplaces</li>
      </ul>

      <div class="works-rule"></div>
      <div class="works-tag">OUR WORKS</div>

      <div class="work-photo work-deck" role="img" aria-label="Wooden deck with pergola and patio chairs surrounded by trees"></div>
      <div class="work-photo work-pool" role="img" aria-label="Aerial view of a small pool framed by light composite decking"></div>
      <div class="work-photo work-firepit" role="img" aria-label="Evening paver patio with a sunken fire pit, lit steps and a pool beyond"></div>

      <div class="phone-box">
        <svg width="46" height="46" viewBox="0 0 24 24" aria-hidden="true"><path fill="#fff" d="M6.6 10.8a15.1 15.1 0 006.6 6.6l2.2-2.2a1 1 0 011-.25 11.4 11.4 0 003.6.57 1 1 0 011 1V20a1 1 0 01-1 1A17 17 0 013 4a1 1 0 011-1h3.5a1 1 0 011 1c0 1.25.2 2.45.57 3.57a1 1 0 01-.25 1z"/></svg>
      </div>
      <div class="phone-number">206-555-0148</div>

      <div class="contact contact-email">
        <svg viewBox="0 0 24 24" aria-hidden="true"><rect x="2" y="5" width="20" height="14" rx="1.5" fill="#fff"/><path d="M3 6.5l9 6.5 9-6.5" stroke="var(--orange)" stroke-width="1.8" fill="none"/></svg>
        info@cedarlinebuilders.com
      </div>
      <div class="contact contact-web">
        <svg viewBox="0 0 24 24" aria-hidden="true" fill="none" stroke="#fff" stroke-width="1.6"><circle cx="12" cy="12" r="9"/><ellipse cx="12" cy="12" rx="4" ry="9"/><path d="M3 12h18M4.5 7.5h15M4.5 16.5h15"/></svg>
        www.cedarlinebuilders.com
      </div>
    </div>
  </div>
</div>
</body>
</html>
```